Veldmark Supplies Business Card

Professional business card that stand out to our potential customers. Front and back with clean modern design

Industry/Entity Type

Oil and gas

Contact Information for Business Card

Name, address, website , office phone and cell number

Requirements
Must have
• Editable files for each employee

```html
<!DOCTYPE html>
<html lang="en">
<head>
<meta charset="utf-8">
<title>Veldmark Supplies Business Card</title>
<link href="https://fonts.googleapis.com/css2?family=Montserrat:wght@400;500;700;800&display=swap" rel="stylesheet">
<style>
  :root {
    --sky: #0bafd3;
    --signal-red: #e32227;
    --ink: #1c1c1c;
    --paper: #ffffff;
    --backdrop: #3a3a3a;
  }
  * { box-sizing: border-box; margin: 0; padding: 0; }
  html, body { width: 1200px; height: 1200px; overflow: hidden; }
  body {
    background: var(--backdrop);
    font-family: "Montserrat", sans-serif;
    position: relative;
  }
  .card {
    position: absolute;
    left: 150px;
    width: 900px;
    height: 514px;
    border-radius: 36px;
    overflow: hidden;
  }
  .card-front { top: 50px; background: var(--sky); }
  .card-back { top: 620px; background: var(--paper); }

  .front-brand {
    position: absolute;
    inset: 0;
    display: flex;
    align-items: center;
    justify-content: center;
    gap: 22px;
  }
  .brand-square {
    width: 46px; height: 46px;
    background: var(--paper);
  }
  .brand-name {
    font-weight: 800;
    text-transform: uppercase;
    letter-spacing: 2px;
    white-space: nowrap;
  }
  .front-brand .brand-name { color: var(--paper); font-size: 52px; }

  .waves { position: absolute; inset: 0; }

  .back-brand {
    position: absolute;
    top: 70px;
    left: 0; right: 0;
    text-align: center;
    color: var(--signal-red);
    font-size: 44px;
  }
  .holder {
    position: absolute;
    top: 205px;
    right: 495px;
    text-align: right;
    white-space: nowrap;
  }
  .holder-name { color: var(--signal-red); font-weight: 700; font-size: 30px; line-height: 36px; }
  .holder-title { color: var(--ink); font-weight: 500; font-size: 19px; margin-top: 4px; }
  .divider {
    position: absolute;
    left: 425px; top: 180px;
    width: 2px; height: 124px;
    background: var(--signal-red);
  }
  .contacts {
    position: absolute;
    left: 450px; top: 178px;
    list-style: none;
    color: var(--ink);
    font-size: 18px;
    line-height: 31px;
    white-space: nowrap;
  }
  .contacts li { display: flex; align-items: center; gap: 12px; }
  .contacts svg { width: 17px; height: 17px; fill: var(--sky); flex: none; }
  .address {
    position: absolute;
    top: 332px; left: 0; right: 0;
    text-align: center;
    color: var(--ink);
    font-size: 18px;
    white-space: nowrap;
  }
</style>
</head>
<body>
  <section class="card card-front">
    <div class="front-brand">
      <span class="brand-square"></span>
      <span class="brand-name">Veldmark Supplies</span>
    </div>
  </section>

  <section class="card card-back">
    <svg class="waves" viewBox="0 0 900 514" aria-hidden="true">
      <path d="M0 514 L0 472 C250 405 600 410 900 292 L900 514 Z" fill="var(--sky)"/>
      <path d="M500 398 C700 385 860 325 900 215 L900 232 C860 342 700 394 500 398 Z" fill="var(--sky)"/>
      <path d="M560 386 C720 362 860 292 900 150 L900 188 C850 312 720 372 560 386 Z" fill="var(--signal-red)"/>
    </svg>

    <div class="brand-name back-brand">Veldmark Supplies</div>

    <div class="holder">
      <div class="holder-name">Daran Holloway</div>
      <div class="holder-title">President</div>
    </div>
    <div class="divider"></div>

    <ul class="contacts">
      <li><svg viewBox="0 0 24 24"><path d="M3 8c0-2 3-4 9-4s9 2 9 4v2h-5V8H8v2H3zM6 12h12l2 8H4z"/></svg>+1.555.210.0400 x123</li>
      <li><svg viewBox="0 0 24 24"><path d="M6 2l4 4-2 3c1 3 4 6 7 7l3-2 4 4-3 4C10 22 2 14 2 5z"/></svg>+1.555.014.782</li>
      <li><svg viewBox="0 0 24 24"><path d="M2 5h20v2l-10 6L2 7zM2 9l10 6 10-6v10H2z"/></svg>info@veldmarksupplies.com</li>
      <li><svg viewBox="0 0 24 24"><circle cx="12" cy="12" r="10"/></svg>www.veldmarksupplies.com</li>
    </ul>

    <p class="address">42 Ridgeline Plaza Harlow Creek, TX 79701 USA</p>
  </section>
</body>
</html>
```